Business Cards for IT Consulting Company (Managed Service Provider)

I am looking to have some business cards printed and would like some designs. We are an IT Consulting company based in Vancouver BC. I would like a nice clean and modern look to the cards. I have uploaded all the versions of my logo so parts can be used as needed. Here is a snippit from our website homepage:

Quillbrook Networks Ltd. is an IT Solutions Partner located in Vancouver BC, Canada. We offer IT solutions and support to customers in the greater Vancouver Area. With expertise in Microsoft platforms, as well as Linux and Mac OSX and over 12 years experience in the IT industry, Quillbrook Networks is dedicated to offering our clients top quality service and products. We take pride in the solutions we offer our customers. The greatest compliment a client can give us is to recommend our services.

Quillbrook Networks Ltd. offers a wide range of IT services from onsite service to remote support and managed service solutions. This allows clients to choose the support path that best suits their company’s needs. Supporting many different sized companies from small to enterprise level over the past 12 years Quillbrook Networks has the experience and expertise needed to ensure things run smoothly. Allowing our clients to focus on doing business.

Revolutionizing the way IT services are delivered.

Quillbrook Networks is dedicated to providing our clients with IT solutions that work and grow with them for years to come. This philosophy helps save money in the long run instead of replacing equipment constantly. Far too often IT solutions are not well thought out and while possibly solving the problem at hand, require replacement due to growth or quality within a very short time frame. Quillbrook Networks takes pride in providing solutions that will last and be able to accommodate growth without the need for replacement.

Industry/Entity Type

Information Technology

Contact Information for Business Card

Quillbrook Networks Ltd.
(Employee Name)
Eml: (Employees Email Address)
Web: quillbrook.me
Ph: 604-555-0148

Font styles to use
Serif
Sans Serif

Requirements
Must have
• The Company logo and company colors.
Nice to have
• - Our tag line: "Revolutionizing IT Services" or "Revolutionizing the way IT services are delivered."
• - Also I really like the idea of nature and technology together blending which is sort of where my logo came from so integrating that somehow onto the business cards would be great.

```html
<!DOCTYPE html>
<html lang="en">
<head>
<meta charset="utf-8">
<title>Quillbrook Networks Ltd. – Business Cards</title>
<link href="https://fonts.googleapis.com/css2?family=Roboto:ital,wght@0,400;0,500;0,700;1,400&display=swap" rel="stylesheet">
<style>
  :root {
    --backdrop: #a9a7a8;
    --card-dark: #1d1d1e;
    --card-light: #f3f3f3;
    --brand-blue: #1a8fd6;
    --brand-grey: #4a4a4c;
    --text-grey: #3c3c3c;
    --text-light: #e8e8e8;
  }
  * { margin: 0; padding: 0; box-sizing: border-box; }
  html, body { width: 1200px; height: 1200px; overflow: hidden; }
  body {
    background: var(--backdrop);
    font-family: "Roboto", Arial, sans-serif;
    position: relative;
  }
  .card { position: absolute; width: 712px; overflow: hidden; }
  .card--front { left: 238px; top: 118px; height: 419px; background: var(--card-dark); }
  .card--back { left: 231px; top: 645px; height: 415px; background: var(--card-light); }

  .brand-name {
    position: absolute;
    color: var(--brand-blue);
    font-weight: 500;
    line-height: 1;
    letter-spacing: 0.5px;
  }
  .brand-name .brand-word { display: block; font-size: 58px; text-transform: lowercase; }
  .brand-name .brand-suffix { display: block; font-size: 24px; margin-top: 4px; text-transform: uppercase; }
  .brand-mark { position: absolute; background: var(--brand-blue); border-radius: 50%; }

  .card--front .brand-mark { left: 112px; top: 150px; width: 80px; height: 80px; }
  .card--front .brand-name { left: 242px; top: 150px; }

  .front-tagline {
    position: absolute; left: 0; right: 0; top: 378px;
    display: flex; align-items: center; justify-content: center; gap: 16px;
    color: var(--text-light); font-size: 18px;
  }
  .front-tagline .rule { width: 110px; height: 3px; background: var(--brand-blue); }

  .card--back .brand-mark { left: 298px; top: 56px; width: 66px; height: 66px; }
  .card--back .brand-name { left: 396px; top: 58px; }
  .card--back .brand-name .brand-word { font-size: 50px; }
  .card--back .brand-name .brand-suffix { font-size: 21px; }

  .person { position: absolute; left: 39px; top: 68px; }
  .person-name { color: var(--brand-blue); font-size: 26px; font-weight: 500; }
  .person-title { color: var(--text-grey); font-size: 17px; font-style: italic; margin-top: 6px; }

  .contact-list { position: absolute; left: 38px; top: 229px; list-style: none; }
  .contact-list li {
    display: flex; align-items: center; gap: 16px;
    height: 27px; color: var(--text-grey); font-size: 18px;
  }
  .contact-list svg { width: 19px; height: 16px; fill: var(--brand-blue); }

  .back-waves { position: absolute; left: 0; top: 0; width: 712px; height: 415px; }
  .back-tagline {
    position: absolute; right: 31px; top: 335px;
    color: #fff; font-size: 18px; line-height: 25px; text-align: right;
  }
</style>
</head>
<body>

<section class="card card--front" aria-label="Card front">
  <span class="brand-mark"></span>
  <div class="brand-name">
    <span class="brand-word">Quillbrook</span>
    <span class="brand-suffix">Networks Ltd.</span>
  </div>
  <div class="front-tagline">
    <span class="rule"></span>
    <span>Revolutionizing IT Services</span>
    <span class="rule"></span>
  </div>
</section>

<section class="card card--back" aria-label="Card back">
  <svg class="back-waves" viewBox="0 0 712 415" aria-hidden="true">
    <path fill="#1a8fd6" d="M0,378 C150,398 300,382 420,302 C520,237 620,224 712,224 L712,415 L0,415 Z"/>
    <path fill="#4a4a4c" d="M0,335 C140,360 280,350 400,270 C500,210 600,205 712,208 L712,222 C610,220 520,232 430,292 C310,372 150,382 0,362 Z"/>
  </svg>

  <div class="person">
    <p class="person-name">Daniel Hart</p>
    <p class="person-title">Managing Director</p>
  </div>

  <span class="brand-mark"></span>
  <div class="brand-name">
    <span class="brand-word">Quillbrook</span>
    <span class="brand-suffix">Networks Ltd.</span>
  </div>

  <ul class="contact-list">
    <li>
      <svg viewBox="0 0 20 16" aria-hidden="true"><path d="M2,5 C2,2 6,1 10,1 C14,1 18,2 18,5 L15,6 L14,4 L6,4 L5,6 Z M4,8 L16,8 L18,15 L2,15 Z M10,9.5 A2.5,2.5 0 1,0 10,14.5 A2.5,2.5 0 1,0 10,9.5 Z"/></svg>
      <span>604-555-0148</span>
    </li>
    <li>
      <svg viewBox="0 0 20 16" aria-hidden="true"><path fill-rule="evenodd" d="M10,1 A7,7 0 1,0 10,15 A7,7 0 1,0 10,1 Z M10,2.5 A5.5,5.5 0 0,1 15.4,7.2 L12.4,7.2 C12.3,5.3 11.4,3.5 10,2.5 Z M10,2.5 C8.6,3.5 7.7,5.3 7.6,7.2 L4.6,7.2 A5.5,5.5 0 0,1 10,2.5 Z M4.6,8.8 L7.6,8.8 C7.7,10.7 8.6,12.5 10,13.5 A5.5,5.5 0 0,1 4.6,8.8 Z M12.4,8.8 L15.4,8.8 A5.5,5.5 0 0,1 10,13.5 C11.4,12.5 12.3,10.7 12.4,8.8 Z M9.1,7.2 C9.2,5.8 9.5,4.7 10,4 C10.5,4.7 10.8,5.8 10.9,7.2 Z M9.1,8.8 L10.9,8.8 C10.8,10.2 10.5,11.3 10,12 C9.5,11.3 9.2,10.2 9.1,8.8 Z"/></svg>
      <span>www.quillbrook.me</span>
    </li>
    <li>
      <svg viewBox="0 0 20 16" aria-hidden="true"><path d="M1,2 L19,2 L19,14 L1,14 Z M3,4 L10,9 L17,4 L17,12 L13,8.5 L10,11 L7,8.5 L3,12 Z" fill-rule="evenodd"/></svg>
      <span>support@quillbrook.me</span>
    </li>
  </ul>

  <p class="back-tagline">Revolutionizing the<br>way IT services are delivered</p>
</section>

</body>
</html>
```